Re-style home page - eye-catching and unique design for social commerce website

We need a new concept design for BrinoKet's home page.
We don't want to make huge changes but creating a more professional and eye-catching style.

We need to look very serious like a professional services company and in the same time to look like a social network for e-commerce.

Our logo is very captive and you can use to creating something of harmonious.

This is a re-style and I'm excepted to see unique and fresh design like Glimmora.

Target Market(s)

e-commerce and social

Industry/Entity Type

Social

Number of Pages Required

1 page

Font styles to use
Serif
Sans Serif

Requirements
Must have
• An eye-catching result.
• Search bar with logo and Login How it works and business
• The slogan with login and signup.
• Footer links.
Nice to have
• I would like to open the home page and see only two clear ways:
• -Consumer
• --Search
• --The slogan
• --Login and Signup
• --How it works
• -Business
• --Go to Business area
• Background: City, Shopping.
Should not have
• Scrollbar style!

```html
<!DOCTYPE html>
<html lang="en">
<head>
<meta charset="utf-8">
<title>BrinoKet – Shop directly from your profile</title>
<link href="https://fonts.googleapis.com/css2?family=Figtree:wght@400;500;600;700&display=swap" rel="stylesheet">
<style>
:root{
  --bar:#222222;
  --bar-deep:#1b1a19;
  --white:#ffffff;
  --ink:#111111;
  --panel:rgba(18,18,18,.86);
  --btn-blue:#4a6bb0;
  --btn-blue-dark:#3a5797;
  --orange:#f2663a;
  --amber:#f0a040;
  --yellow:#f2e24a;
  --pink:#e3385f;
  --violet:#6d72d8;
  --olive:#c4c86e;
  --slate:#4c5c8e;
  --indigo:#4448b8;
  --mustard:#c3bb2c;
}
*{box-sizing:border-box;margin:0;padding:0}
html,body{width:1200px;height:936px;overflow:hidden}
body{font-family:"Figtree",Arial,sans-serif;color:var(--white);position:relative;background:#9a9a98}
.backdrop{position:absolute;inset:0;background:
  radial-gradient(ellipse at 20% 70%,rgba(40,34,30,.55),transparent 45%),
  radial-gradient(ellipse at 85% 65%,rgba(70,45,25,.5),transparent 40%),
  linear-gradient(180deg,#c9cbcc 0%,#a9abab 45%,#8a8a88 75%,#6e6c6a 100%)}
.site-header{position:absolute;top:0;left:0;width:1200px;height:69px;background:var(--bar)}
.brand{position:absolute;left:116px;top:12px;font-size:38px;font-weight:700;letter-spacing:-.5px;display:flex;align-items:center;gap:10px}
.brand-mark{width:22px;height:22px;border-radius:50%;background:var(--amber)}
.search{position:absolute;left:463px;top:16px;width:253px;height:36px;background:var(--white);border-radius:3px;display:flex;align-items:center;padding:0 9px;justify-content:space-between}
.search span{color:#9a9a9a;font-size:14px}
.nav{position:absolute;top:22px;left:729px;display:flex;align-items:center;font-size:16px;font-weight:500}
.nav a{color:var(--white);text-decoration:none}
.nav .how{margin-right:21px}.nav .biz{margin-right:25px}.nav .login{margin-right:12px}
.nav .signup{border:2px solid #cfcfcf;padding:1px 7px;border-radius:2px;margin-top:-2px}
.headline{position:absolute;top:195px;left:0;width:1200px;text-align:center;color:var(--ink);font-size:33px;font-weight:700;letter-spacing:.2px}
.feed{position:absolute;left:174px;top:258px;width:852px;height:461px;background:var(--panel)}
.feed h2{text-align:center;font-size:30px;font-weight:400;margin-top:14px;letter-spacing:.3px}
.tags{margin-top:13px;display:flex;flex-direction:column;gap:10px;align-items:center}
.row{display:flex;gap:9px}
.tag{position:relative;height:45px;background:var(--white);border-radius:4px;color:var(--ink);font-size:15.5px;font-weight:500;display:flex;align-items:center;padding:0 10px 0 62px;white-space:nowrap;overflow:hidden}
.tag::before{content:"";position:absolute;left:0;top:0;bottom:0;width:58px;background:var(--c);clip-path:polygon(0 0,40px 0,58px 100%,0 100%)}
.tag svg{position:absolute;left:8px;top:9px}
.tagline{text-align:center;font-size:21px;margin-top:21px}
.connect{display:flex;width:208px;height:40px;margin:14px auto 0;background:linear-gradient(var(--btn-blue),var(--btn-blue-dark));border:1px solid #2f4a85;align-items:center;font-size:14px;font-weight:700}
.connect .sq{width:42px;height:38px;border-right:1px solid #2f4a85;display:flex;align-items:center;justify-content:center}
.connect .sq i{width:14px;height:14px;background:var(--white);display:block}
.connect span{flex:1;text-align:center}
.site-footer{position:absolute;left:0;top:876px;width:1200px;height:60px;background:var(--bar-deep);display:flex;justify-content:center;align-items:center;gap:21px;font-size:16px;font-weight:500}
.site-footer a{color:var(--white);text-decoration:none}
</style>
</head>
<body>
<div class="backdrop" role="img" aria-label="Blurred photo of shoppers walking through a bright glass city concourse"></div>

<header class="site-header">
  <div class="brand"><span>BrinoKet</span><span class="brand-mark"></span></div>
  <div class="search"><span>Search...</span>
    <svg width="20" height="20" viewBox="0 0 20 20"><circle cx="8" cy="8" r="6" fill="none" stroke="#a8a8a8" stroke-width="3"/><line x1="12.5" y1="12.5" x2="18" y2="18" stroke="#a8a8a8" stroke-width="3.5" stroke-linecap="round"/></svg>
  </div>
  <nav class="nav">
    <a class="how" href="#">How it works</a>
    <a class="biz" href="#">business</a>
    <a class="login" href="#">Log in</a>
    <a class="signup" href="#">Sign up now!</a>
  </nav>
</header>

<h1 class="headline">SHOP DIRECTLY FROM YOUR PROFILE</h1>

<section class="feed">
  <h2>Setup Your Feed</h2>
  <div class="tags">
    <div class="row">
      <div class="tag" style="--c:var(--orange)"><svg width="28" height="28"><circle cx="14" cy="14" r="12" fill="none" stroke="#fff" stroke-width="2"/></svg>Active Life</div>
      <div class="tag" style="--c:var(--yellow)"><svg width="28" height="28"><rect x="3" y="5" width="22" height="18" rx="2" fill="none" stroke="#fff" stroke-width="2"/></svg>Education</div>
      <div class="tag" style="--c:var(--amber);padding-right:12px"><svg width="28" height="28"><rect x="3" y="5" width="22" height="18" rx="2" fill="none" stroke="#fff" stroke-width="2"/></svg>Automotive</div>
      <div class="tag" style="--c:var(--pink)"><svg width="28" height="28"><rect x="3" y="5" width="22" height="18" rx="2" fill="none" stroke="#fff" stroke-width="2"/></svg>Nightlife</div>
      <div class="tag" style="--c:var(--violet)"><svg width="28" height="28"><rect x="3" y="6" width="22" height="16" rx="2" fill="none" stroke="#fff" stroke-width="2"/></svg>Mass Media</div>
    </div>
    <div class="row">
      <div class="tag" style="--c:var(--amber)"><svg width="28" height="28"><rect x="3" y="5" width="22" height="18" rx="3" fill="none" stroke="#fff" stroke-width="2"/></svg>Public Services &amp; Government</div>
      <div class="tag" style="--c:var(--olive)"><svg width="28" height="28"><rect x="6" y="3" width="16" height="22" rx="2" fill="none" stroke="#fff" stroke-width="2"/></svg>Professional Services</div>
      <div class="tag" style="--c:var(--olive)"><svg width="28" height="28"><rect x="3" y="4" width="22" height="20" rx="2" fill="none" stroke="#fff" stroke-width="2"/></svg>Even Planning &amp; Services</div>
    </div>
    <div class="row">
      <div class="tag" style="--c:var(--slate)"><svg width="28" height="28"><rect x="6" y="3" width="16" height="22" fill="none" stroke="#fff" stroke-width="2"/></svg>Financial Services</div>
      <div class="tag" style="--c:var(--pink)"><svg width="28" height="28"><rect x="5" y="6" width="18" height="18" rx="2" fill="none" stroke="#fff" stroke-width="2"/></svg>Restaurants</div>
      <div class="tag" style="--c:var(--pink)"><svg width="28" height="28"><path d="M4 14 L14 5 L24 14 V24 H4 Z" fill="none" stroke="#fff" stroke-width="2"/></svg>Home Services</div>
      <div class="tag" style="--c:var(--pink)"><svg width="28" height="28"><rect x="4" y="4" width="20" height="20" rx="3" fill="none" stroke="#fff" stroke-width="2"/></svg>Arts &amp; Entertainment</div>
    </div>
    <div class="row">
      <div class="tag" style="--c:var(--indigo)"><svg width="28" height="28"><rect x="3" y="7" width="22" height="16" rx="2" fill="none" stroke="#fff" stroke-width="2"/><path d="M14 11v8M10 15h8" stroke="#fff" stroke-width="2"/></svg>Health &amp; Medical</div>
      <div class="tag" style="--c:var(--slate)"><svg width="28" height="28"><path d="M4 14 L14 5 L24 14 V24 H4 Z" fill="none" stroke="#fff" stroke-width="2"/></svg>Real Estate</div>
      <div class="tag" style="--c:var(--orange)"><svg width="28" height="28"><rect x="5" y="3" width="18" height="22" fill="none" stroke="#fff" stroke-width="2"/></svg>Hotel</div>
      <div class="tag" style="--c:var(--yellow)"><svg width="28" height="28"><rect x="4" y="6" width="20" height="18" rx="3" fill="none" stroke="#fff" stroke-width="2"/></svg>Food</div>
      <div class="tag" style="--c:var(--indigo)"><svg width="28" height="28"><circle cx="14" cy="14" r="11" fill="none" stroke="#fff" stroke-width="2"/></svg>Local Services</div>
    </div>
    <div class="row">
      <div class="tag" style="--c:var(--mustard)"><svg width="28" height="28"><circle cx="14" cy="14" r="11" fill="none" stroke="#fff" stroke-width="2"/></svg>Pets</div>
      <div class="tag" style="--c:var(--pink)"><svg width="28" height="28"><rect x="5" y="3" width="18" height="22" rx="3" fill="none" stroke="#fff" stroke-width="2"/></svg>Beauty &amp; Spas</div>
      <div class="tag" style="--c:var(--slate)"><svg width="28" height="28"><rect x="4" y="5" width="20" height="19" rx="2" fill="none" stroke="#fff" stroke-width="2"/></svg>Shopping</div>
    </div>
  </div>
  <p class="tagline">Save your time. Life better.</p>
  <a class="connect"><div class="sq"><i></i></div><span>Login with Connectly</span></a>
</section>

<footer class="site-footer">
  <a href="#">About Us</a><a href="#">Blog</a><a href="#">Business</a><a href="#">Jobs</a><a href="#">Privacy</a><a href="#">FAQ</a><a href="#">Contacts</a>
</footer>
</body>
</html>
```